Card design for orthopaedic surgeons working as The Brightwater Joint Centre

Business cards, letterhead

Colors

Designer to choose colors to be used in the design.

Requirements
Must have
• Late addition.
• Cards letterhead must have logos of
• Crestmoor Lindell College of Surgeons
• Varenwood Bone Health Association
Nice to have
• Back of card to have space for appointment time to be added by hand and some blank space for writing incidental other notes.

```html
<!DOCTYPE html>
<html lang="en">
<head>
<meta charset="utf-8">
<title>The Brightwater Joint Centre – Business Card</title>
<link rel="stylesheet" href="https://fonts.googleapis.com/css2?family=Lato:wght@300;400;700&display=swap">
<style>
  :root {
    --backdrop: #2f2f31;
    --navy: #0a3350;
    --sky: #35a9f0;
    --paper: #ffffff;
    --ink-soft: #e6eef5;
  }
  * { margin: 0; padding: 0; box-sizing: border-box; }
  html, body {
    width: 1200px; height: 866px; overflow: hidden;
    background: var(--backdrop);
    font-family: "Lato", Arial, sans-serif;
  }
  .sheet {
    width: 1200px; height: 866px;
    display: flex; align-items: center; justify-content: center; gap: 40px;
  }
  .card {
    position: relative;
    width: 540px; height: 309px;
    overflow: hidden;
    box-shadow: 0 10px 24px rgba(0,0,0,0.45);
  }
  .card-front { background: var(--paper); }
  .card-back { background: var(--navy); display: flex; align-items: center; justify-content: center; }
  .wave { position: absolute; inset: 0; width: 100%; height: 100%; }

  .brand-name {
    font-weight: 300;
    color: var(--sky);
    letter-spacing: 0.2px;
    white-space: nowrap;
  }
  .card-front .brand-name {
    position: absolute; left: 34px; top: 34px;
    font-size: 21px;
  }
  .card-back .brand-name { font-size: 31px; }

  .person {
    position: absolute; right: 34px; top: 76px;
    text-align: right;
  }
  .person-name { font-size: 24px; font-weight: 400; line-height: 1.05; }
  .person-first { color: var(--sky); }
  .person-last { color: var(--navy); font-weight: 700; }
  .person-role { font-size: 14px; color: var(--navy); letter-spacing: 0.6px; }

  .contact {
    position: absolute; right: 30px; top: 184px;
    list-style: none;
    text-align: right;
    color: var(--ink-soft);
    font-size: 13px; line-height: 19px;
    letter-spacing: 0.3px;
  }
  .contact li { display: flex; justify-content: flex-end; align-items: center; gap: 7px; }
  .contact .icon { width: 11px; height: 11px; fill: var(--sky); flex: none; }
  .contact .no-icon { width: 11px; flex: none; }
</style>
</head>
<body>
<main class="sheet">

  <section class="card card-front" aria-label="Business card front">
    <svg class="wave" viewBox="0 0 540 309" preserveAspectRatio="none" aria-hidden="true">
      <path d="M0,80 C8,140 70,150 240,158 C380,164 470,160 540,156 L540,309 L0,309 Z" fill="var(--navy)"/>
      <path d="M4,58 C12,124 70,136 240,144 C380,150 470,146 540,142" fill="none" stroke="var(--sky)" stroke-width="5"/>
      <path d="M0,92 C14,148 80,158 240,166 C380,172 470,168 540,164" fill="none" stroke="var(--paper)" stroke-width="1.6"/>
    </svg>

    <div class="brand-name">The Brightwater Joint Centre</div>

    <div class="person">
      <div class="person-name"><span class="person-first">Marcus</span> <span class="person-last">Ellery</span></div>
      <div class="person-role">Managing Director</div>
    </div>

    <ul class="contact">
      <li>055-310 782 946
        <svg class="icon" viewBox="0 0 12 12"><path d="M2.5 1h2l1 3-1.5 1a6 6 0 0 0 3 3l1-1.5 3 1v2a1 1 0 0 1-1 1A10 10 0 0 1 1.5 2a1 1 0 0 1 1-1z"/></svg></li>
      <li>hello@brightwaterjoint.com
        <svg class="icon" viewBox="0 0 12 12"><path d="M1 2.5h10v7H1z M1 2.5l5 4 5-4" fill="var(--sky)" stroke="var(--navy)" stroke-width="0.8"/></svg></li>
      <li>www.brightwaterjoint.com
        <svg class="icon" viewBox="0 0 12 12"><circle cx="6" cy="6" r="5"/></svg></li>
      <li>18, Harbourview Lane,<span class="no-icon"></span></li>
      <li>Kestrel Bay 40917<span class="no-icon"></span></li>
    </ul>
  </section>

  <section class="card card-back" aria-label="Business card back">
    <div class="brand-name">The Brightwater Joint Centre</div>
  </section>

</main>
</body>
</html>
```